Carpet cleaning company focused on high quality needs business cards

We are a growing company that just merged with another company and need to design a new business card. We do both residential as well as commercial cleaning. We do carpet, tile & grout, upholstery, hard floors, and stain & pet odor removal. We treat our customers like family and strive to achieve outstanding results with every job.

```html
<!DOCTYPE html>
<html lang="en">
<head>
<meta charset="utf-8">
<title>Brightwell Floor Care – Business Card</title>
<link rel="stylesheet" href="https://fonts.googleapis.com/css2?family=Open+Sans:wght@400;600;700&display=swap">
<style>
  :root {
    --backdrop: #dcdddf;
    --card: #ffffff;
    --ink: #1b1b1b;
    --brand-red: #e8413b;
    --brand-blue: #1b7fc4;
    --panel-tint: #fbf4f3;
    --card-shadow: 0 10px 28px rgba(0,0,0,.22);
  }
  * { box-sizing: border-box; margin: 0; padding: 0; }
  html, body { width: 1200px; height: 780px; overflow: hidden; }
  body {
    background: var(--backdrop);
    font-family: "Open Sans", Arial, sans-serif;
    color: var(--ink);
    position: relative;
  }
  .card {
    position: absolute;
    top: 233px;
    width: 550px;
    height: 314px;
    background: var(--card);
    box-shadow: var(--card-shadow);
    overflow: hidden;
  }
  .card--front { left: 30px; }
  .card--back  { left: 620px; }

  /* Company name */
  .brand { display: flex; align-items: center; gap: 10px; }
  .brand__dot { width: 12px; height: 12px; border-radius: 50%; background: var(--brand-blue); flex: none; }
  .brand__name { font-weight: 600; color: var(--ink); white-space: nowrap; }

  /* Front */
  .card--front .brand { position: absolute; left: 34px; top: 116px; }
  .card--front .brand__name { font-size: 20px; }

  .person { position: absolute; right: 40px; top: 34px; text-align: right; }
  .person__name { font-size: 26px; font-weight: 700; line-height: 1.15; white-space: nowrap; }
  .person__first { color: var(--brand-blue); }
  .person__last  { color: var(--brand-red); }
  .person__title { font-size: 14px; font-weight: 400; margin-top: 2px; }

  .corner-tab { position: absolute; right: 0; top: 0; width: 18px; height: 66px; background: var(--brand-blue); }
  .divider { position: absolute; left: 60px; right: 22px; top: 168px; height: 1.5px; background: var(--brand-red); }

  .contact { position: absolute; left: 34px; top: 188px; list-style: none; font-size: 15px; line-height: 1.55; }
  .contact li { display: flex; align-items: center; gap: 9px; }
  .contact svg { width: 14px; height: 14px; flex: none; }

  .address-panel {
    position: absolute; right: 18px; top: 176px; width: 230px; height: 90px;
    background: var(--panel-tint);
  }
  .address { position: absolute; right: 40px; top: 190px; text-align: right; font-size: 14px; line-height: 1.5; font-style: normal; }

  .edge-red { position: absolute; right: 0; top: 66px; width: 18px; bottom: 0; background: var(--brand-red); }
  .base-red { position: absolute; left: 0; right: 0; bottom: 0; height: 8px; background: var(--brand-red); }
  .base-blue { position: absolute; left: 0; right: 18px; bottom: 12px; height: 5px; background: var(--brand-blue); }

  /* Back */
  .card--back .brand { position: absolute; left: 50%; top: 96px; transform: translateX(-50%); gap: 14px; }
  .card--back .brand__dot { width: 18px; height: 18px; }
  .card--back .brand__name { font-size: 34px; }

  .services { position: absolute; left: 26px; right: 26px; top: 212px; text-align: center; }
  .services__heading {
    display: flex; align-items: center; gap: 10px;
    color: var(--brand-red); font-size: 18px; font-weight: 600; margin-bottom: 6px;
  }
  .services__heading::before, .services__heading::after {
    content: ""; flex: 1; height: 1.5px; background: var(--brand-red);
  }
  .services__text { font-size: 12.5px; font-weight: 600; line-height: 1.5; }
</style>
</head>
<body>

  <section class="card card--front" aria-label="Business card front">
    <div class="corner-tab"></div>
    <div class="edge-red"></div>
    <div class="address-panel"></div>

    <div class="brand">
      <span class="brand__dot"></span>
      <span class="brand__name">Brightwell Floor Care</span>
    </div>

    <div class="person">
      <p class="person__name"><span class="person__first">Marta</span> <span class="person__last">Kovalenko</span></p>
      <p class="person__title">Managing Director</p>
    </div>

    <div class="divider"></div>

    <ul class="contact">
      <li>
        <svg viewBox="0 0 16 16" aria-hidden="true"><path fill="#1b7fc4" d="M3.6 1.2 6 3.8 4.7 5.6c.9 2 2.5 3.6 4.5 4.6l1.8-1.3 2.6 2.4-1.3 2.3C7 13.5 2.6 9 1.3 3.1z"/></svg>
        (555) 014-2291
      </li>
      <li>
        <svg viewBox="0 0 16 16" aria-hidden="true"><rect x="1" y="3" width="14" height="10" rx="1" fill="#1b7fc4"/><path d="M1.5 3.5 8 9l6.5-5.5" stroke="#fff" stroke-width="1.3" fill="none"/></svg>
        info@brightwellcare.com
      </li>
      <li>
        <svg viewBox="0 0 16 16" aria-hidden="true"><circle cx="8" cy="8" r="7" fill="#1b7fc4"/><path d="M1 8h14M8 1c-3 3.5-3 10.5 0 14M8 1c3 3.5 3 10.5 0 14" stroke="#fff" stroke-width="1" fill="none"/></svg>
        www.brightwellcare.com
      </li>
    </ul>

    <address class="address">418 Linden Ave. Suite 120<br>Brookfield, TX 75010</address>

    <div class="base-blue"></div>
    <div class="base-red"></div>
  </section>

  <section class="card card--back" aria-label="Business card back">
    <div class="brand">
      <span class="brand__dot"></span>
      <span class="brand__name">Brightwell Floor Care</span>
    </div>

    <div class="services">
      <h2 class="services__heading">Our services</h2>
      <p class="services__text">We do both residential as well as commercial cleaning.<br>
      We do carpet, tile &amp; grout, upholstery, hard floors, and stain &amp; pet odor removal.</p>
    </div>
  </section>

</body>
</html>
```